Detail Shop Business card design

i need a business card design for my new detailing company called 'Brisk's Polish Works'. i want an all black and white design . simple, direct and to the point. i want the designer to choose a fitting font to match the logothe front should have logo, address, phone and email and the back side should have a slogan and text indicating that we offer services on anything including cars, trucks, motorcycles and RVs. slogan will read "we take pride in your ride"
maybe also very small on the back side the IG icon with Brisks_Polish_Works

phone 208.417.6352
address 3847 E Larkin Ave
Spokane WA 99214
email: BrisksPolish@mailvexo.com

Target Market(s)

all ages , auto enthusiasts

Industry/Entity Type

Automotive

Contact Information for Business Card

the front should have logo, address, phone and email and the back side should have a slogan and text indicating that we offer services on anything including cars, trucks, motorcycles and RVs. slogan will read "we take pride in your ride"

phone 208.417.6352
address 3847 E Larkin Ave
Spokane WA 99214

Colors
000000
ffffff

Requirements
Must have
• bold font and very simple design with good spacing
Nice to have
• anything creative from the designer indicating we service any types of vehicles
Should not have
• any colors ,

```html
<!DOCTYPE html>
<html lang="en">
<head>
<meta charset="utf-8">
<title>Brisk's Polish Works – Business Card</title>
<link rel="stylesheet" href="https://fonts.googleapis.com/css2?family=Roboto+Slab:wght@300;400;700;800&display=swap">
<style>
  :root {
    --stage: #4a4a4a;
    --card-white: #ffffff;
    --card-black: #111111;
    --ink-black: #000000;
    --ink-white: #ffffff;
    --ghost: rgba(255,255,255,0.06);
    --slab: "Roboto Slab", Georgia, serif;
  }
  * { box-sizing: border-box; margin: 0; padding: 0; }
  html, body { width: 1200px; height: 1000px; overflow: hidden; }
  body { background: var(--stage); position: relative; font-family: var(--slab); }

  .card {
    position: absolute;
    left: 280px;
    width: 640px;
    height: 366px;
    border-radius: 24px;
    overflow: hidden;
  }

  /* Front */
  .card-front { top: 70px; background: var(--card-white); color: var(--ink-black); }
  .brand-mark {
    position: absolute; left: 60px; top: 54px;
    display: flex; align-items: center; gap: 14px;
  }
  .brand-mark .dot {
    width: 46px; height: 46px; border-radius: 50%; background: var(--ink-black);
  }
  .brand-name {
    font-family: var(--slab); font-weight: 800; font-size: 30px;
    line-height: 1.05; color: var(--ink-black); letter-spacing: 0.5px;
  }
  .contact {
    position: absolute; right: 46px; bottom: 40px;
    font-weight: 700; font-size: 17px; line-height: 1.3;
    list-style: none;
  }
  .contact li { display: flex; align-items: flex-start; gap: 8px; }
  .contact svg { width: 14px; height: 14px; margin-top: 4px; flex: none; }
  .contact .spacer { width: 14px; flex: none; }

  /* Back */
  .card-back { top: 520px; background: var(--card-black); color: var(--ink-white); }
  .ghost-mark {
    position: absolute; left: 50%; top: 50%; transform: translate(-50%, -50%);
    width: 300px; height: 300px; border-radius: 50%;
    border: 26px solid var(--ghost);
    display: flex; align-items: center; justify-content: center; text-align: center;
  }
  .ghost-mark span {
    font-weight: 800; font-size: 40px; line-height: 1.05; color: var(--ghost);
  }
  .slogan {
    position: absolute; top: 118px; left: 0; right: 0; text-align: center;
    font-weight: 800; font-size: 32px; letter-spacing: 0.5px;
  }
  .services-label {
    position: absolute; top: 206px; left: 0; right: 0; text-align: center;
    font-weight: 300; font-size: 15px; letter-spacing: 1.5px;
  }
  .services-list {
    position: absolute; top: 232px; left: 0; right: 0; text-align: center;
    font-weight: 700; font-size: 20px; letter-spacing: 1px;
  }
  .services-list .sep { margin: 0 8px; }
  .social {
    position: absolute; right: 36px; bottom: 28px;
    display: flex; align-items: center; gap: 8px;
    font-weight: 400; font-size: 11px;
  }
  .social .square { width: 16px; height: 16px; border-radius: 3px; background: var(--ink-white); }
</style>
</head>
<body>

<section class="card card-front" aria-label="Business card front">
  <div class="brand-mark">
    <span class="dot"></span>
    <span class="brand-name">Brisk's<br>Polish Works</span>
  </div>
  <ul class="contact">
    <li>
      <svg viewBox="0 0 24 24" aria-hidden="true"><path fill="currentColor" d="M12 2a7 7 0 0 0-7 7c0 5 7 13 7 13s7-8 7-13a7 7 0 0 0-7-7zm0 9.5A2.5 2.5 0 1 1 12 6.5a2.5 2.5 0 0 1 0 5z"/></svg>
      <span>3847 E Larkin Ave</span>
    </li>
    <li><span class="spacer"></span><span>Spokane WA 99214</span></li>
    <li>
      <svg viewBox="0 0 24 24" aria-hidden="true"><path fill="currentColor" d="M6.6 10.8a15 15 0 0 0 6.6 6.6l2.2-2.2a1 1 0 0 1 1-.25 11.4 11.4 0 0 0 3.6.57 1 1 0 0 1 1 1V20a1 1 0 0 1-1 1A17 17 0 0 1 3 4a1 1 0 0 1 1-1h3.5a1 1 0 0 1 1 1c0 1.25.2 2.45.57 3.57a1 1 0 0 1-.25 1z"/></svg>
      <span>208.417.6352</span>
    </li>
    <li>
      <svg viewBox="0 0 24 24" aria-hidden="true"><path fill="currentColor" d="M3 5h18a1 1 0 0 1 1 1v12a1 1 0 0 1-1 1H3a1 1 0 0 1-1-1V6a1 1 0 0 1 1-1zm9 7.5L4 7.5V9l8 5 8-5V7.5z"/></svg>
      <span>BrisksPolish@mailvexo.com</span>
    </li>
  </ul>
</section>

<section class="card card-back" aria-label="Business card back">
  <div class="ghost-mark" aria-hidden="true"><span>Brisk's<br>Polish Works</span></div>
  <h1 class="slogan">WE TAKE PRIDE IN YOUR RIDE</h1>
  <p class="services-label">SERVICES OFFERED ON:</p>
  <p class="services-list">CARS<span class="sep">•</span>TRUCKS<span class="sep">•</span>MOTORCYCLES<span class="sep">•</span>RVS</p>
  <div class="social">
    <span class="square"></span>
    <span>Brisks_Polish_Works</span>
  </div>
</section>

</body>
</html>
```